Custom unique Stationary design for Logistics company

We need a custom, unique , elegant and luxurious full stationary design using our new logo, following these guidelines:
1- Business card: double sided, both sides uses the navy blue as the background main color (same as the code of the navy blue used in our logo).
2- envelope and folder: also use the same navy blue as the main background color.
3- book cover( notepad cover) : same thing with the navy blue
4- letterhead: feel free to use the combination of the colors in our logo.
5- rest of the items are up to your creativity

Target Market(s)

corporates and other businesses

Industry/Entity Type

Logistics and heavy machines contractors

Requirements
Must have
• Letterhead, business card, envelope, notepad cover, paper, file
Nice to have
• navy blue to be main background color for business card, envelope, notepad cover

```html
<!DOCTYPE html>
<html lang="en">
<head>
<meta charset="utf-8">
<title>Northfold Freight – Business Card</title>
<link rel="stylesheet" href="https://fonts.googleapis.com/css2?family=Exo+2:wght@400;500;600&display=swap">
<style>
  :root {
    --page-bg: #e7e4df;
    --card-light: #e3e7ea;
    --navy-light: #284d6e;
    --navy-mid: #0d2540;
    --navy-deep: #050f1e;
    --accent-red: #c9301c;
    --text-light: #d9e0e7;
    --text-navy: #1d3550;
  }
  * { margin: 0; padding: 0; box-sizing: border-box; }
  html, body {
    width: 1200px; height: 969px; overflow: hidden;
    background: var(--page-bg);
    font-family: "Exo 2", "Segoe UI", sans-serif;
  }
  .card {
    position: absolute; left: 70px; top: 182px;
    width: 1060px; height: 604px;
    border-radius: 26px; overflow: hidden;
    background: var(--card-light);
    box-shadow: 0 14px 40px rgba(0,0,0,0.18);
  }
  .card-shape { position: absolute; inset: 0; }
  .holder {
    position: absolute; right: 74px; top: 62px; text-align: right;
  }
  .holder-name {
    color: var(--accent-red); font-size: 38px; font-weight: 400;
    letter-spacing: 0.5px; line-height: 1;
  }
  .holder-title {
    color: var(--text-navy); font-size: 21px; font-weight: 500; margin-top: 10px;
  }
  .brand {
    position: absolute; left: 60px; top: 190px;
    color: var(--text-light); font-size: 46px; font-weight: 600;
    letter-spacing: 2px; line-height: 1;
  }
  .address {
    position: absolute; left: 49px; top: 345px;
    color: var(--text-light); font-size: 22px; line-height: 30px;
  }
  .contacts {
    position: absolute; left: 49px; top: 432px; list-style: none;
    color: var(--text-light); font-size: 22px;
  }
  .contacts li { display: flex; align-items: center; height: 30px; }
  .contacts svg { width: 20px; height: 20px; margin-right: 14px; fill: var(--accent-red); }
</style>
</head>
<body>
  <div class="card">
    <svg class="card-shape" viewBox="0 0 1060 604" width="1060" height="604" aria-hidden="true">
      <defs>
        <radialGradient id="navyFill" cx="0.2" cy="0.35" r="0.9">
          <stop offset="0" stop-color="var(--navy-light)"/>
          <stop offset="0.55" stop-color="var(--navy-mid)"/>
          <stop offset="1" stop-color="var(--navy-deep)"/>
        </radialGradient>
      </defs>
      <path d="M548,62 C770,220 990,410 1012,525 C1022,575 995,604 958,604 L895,604 C960,598 998,570 990,522 C955,400 760,215 548,62 Z" fill="var(--accent-red)"/>
      <path d="M0,0 H439 C690,170 940,380 990,520 C1000,570 962,600 895,604 H0 Z" fill="url(#navyFill)"/>
    </svg>

    <div class="holder">
      <p class="holder-name">DANIEL REEVES</p>
      <p class="holder-title">President</p>
    </div>

    <p class="brand">NORTHFOLD FREIGHT</p>

    <p class="address">4120 Birchwood Drive<br>Fairbanks, Alaska 99701</p>

    <ul class="contacts">
      <li><svg viewBox="0 0 24 24"><path d="M6.6 10.8a15 15 0 0 0 6.6 6.6l2.2-2.2a1 1 0 0 1 1-.25 11.4 11.4 0 0 0 3.6.57 1 1 0 0 1 1 1V20a1 1 0 0 1-1 1A17 17 0 0 1 3 4a1 1 0 0 1 1-1h3.5a1 1 0 0 1 1 1c0 1.25.2 2.45.57 3.57a1 1 0 0 1-.25 1z"/></svg>555-214-0387</li>
      <li><svg viewBox="0 0 24 24"><path d="M7 1h10a2 2 0 0 1 2 2v18a2 2 0 0 1-2 2H7a2 2 0 0 1-2-2V3a2 2 0 0 1 2-2zm0 3v15h10V4z"/></svg>555-618-2290</li>
      <li><svg viewBox="0 0 24 24"><path d="M2 5h20v14H2zm2 2v.5l8 5 8-5V7z"/></svg>info@northfoldfreight.com</li>
      <li><svg viewBox="0 0 24 24"><circle cx="12" cy="12" r="10"/></svg>northfoldfreight.com</li>
    </ul>
  </div>
</body>
</html>
```